Commercial Rooftop Solar business needs a website

We need a website with fantastic appeal for a new company based in Melbourne called Tallow Ridge Energy. We design and install solar energy systems for commercial applications across Australia. Our market is to focus on small to medium businesses looking for solar solutions, but we will also provide our service for residential customers. We would like a beautiful 'front page' feel to our home page, using photographs of solar PV systems and/or natural imagery. Our logo uses the colours orange and black, which could easily be echoed in photographic imagery of sunset and sunrise, for example. The design should communicate quiet confidence and professionalism to a corporate marketplace.

NEW POINTS FOR BRIEF: This design also needs to be flexible to allow for additional future content, including a Support page with sub pages, FAQ's, and a Blog.

As part of this design project, we will require the coding for the website to be completed by the designer.

We have seen some websites, which we like the look and feel of: these are listed below.

brightvanepower.com.au:

• Beautiful images underlaying brief text selling points.
• Simple ‘front cover’ style home page with elegant drop-down menu, stylish simple font style.
• Home page invites exploration through the menu links, rather than trying to provide all the information up front.
• Company logo and name in the top left hand corner, contact details accessible at top right hand, seems consistent in most sites.

kelpworks.com.au

rumbofield.com:
• Same element as the others is the front-page style home page with beautiful images underlying text.

We have a webpage that we started uploading content to. You can use some of the content there in your designs: www.tallowridgeenergy.com.au

Technical Specifications:
PAGES:

Home

About Us

Solutions - Commercial
- Residential

Products - Solar Panels - Vorla Heron, Vorla TELD, Vorla QB
- Solar Inverters - Kestamo, BrilQuill
- Monitoring systems - Dunmere Metrics
- Batteries - RW

- Datasheets have been provided for reference but if it's too much work, you can use generic text and we will provide content later.

Contact Us

FUTURE PAGES (Please consider in structure, where links could be placed):

Support

FAQ's

Blog.

We could provide some content for the Support page soon, but the Blog and FAQ's are future pages which we don't want highlighted in the design as we don't yet have content.

Phone: 1800 7 BIRCH
Email: sales@tallowridgeenergy.com.au

Currently, I do not have images and text available. Please
use placeholders in the meantime. The final text and images will be uploaded for the winner once a winning design has been selected.

Target Market(s)

Primary focus is on small to medium sized business owners. Those owners will have a house which may be suitable for solar so we want to cater to residential deeper in the website.

Industry/Entity Type

Solar Energy

Coding

Coded - Design and coding required

Number of Pages Required

5+ page

Colors
f78f20
0255a3

Requirements
Must have
• Logo as per attachments.
Nice to have
• Logo can have alternate colours Eg. White on Orange or Black etc. provided colour correct logo is shown somewhere eg. footer or contact page.
• In the active site, I'd like to have:
• Very slowly zooming images - barely perceptible.
• Title text that rolls into place
• Subtle movements
• See https://plumtally.com.au/ for example

```html
<!DOCTYPE html>
<html lang="en">
<head>
<meta charset="utf-8">
<title>Tallow Ridge Energy – Solar Energy</title>
<link href="https://fonts.googleapis.com/css2?family=Rajdhani:wght@500;600;700&family=Raleway:wght@400;600;700&family=Open+Sans:wght@400;600&display=swap" rel="stylesheet">
<style>
:root{
  --orange:#f15a24;
  --orange-dark:#d94c18;
  --ink:#2b2b2b;
  --charcoal:#222222;
  --slate:#3b3b3b;
  --mist:#f2f2f2;
  --rule:#cfcfcf;
  --white:#ffffff;
  --text:#555555;
}
*{box-sizing:border-box;margin:0;padding:0}
html,body{width:1200px;height:3689px;overflow:hidden}
body{position:relative;font-family:"Open Sans",Arial,sans-serif;color:var(--text);background:var(--white)}
.abs{position:absolute}
/* hero */
.hero{position:absolute;left:0;top:0;width:1200px;height:669px;overflow:hidden}
.hero-photo{position:absolute;inset:0;background:linear-gradient(180deg,#3d6aa6 0%,#6d93c4 45%,#9fb0bd 70%,#3a4a66 100%)}
.hero-shade{position:absolute;inset:0;background:linear-gradient(90deg,rgba(20,40,80,.55) 0%,rgba(20,40,80,.15) 55%,rgba(0,0,0,0) 100%)}
.navbar{position:absolute;left:44px;top:30px;width:1112px;height:73px;background:var(--charcoal)}
.brand{position:absolute;left:0;top:0;height:73px;width:256px;background:var(--white);clip-path:polygon(0 0,226px 0,256px 50%,226px 100%,0 100%);display:flex;align-items:center;padding-left:20px;gap:10px}
.brand-dot{width:30px;height:30px;border-radius:50%;background:var(--orange);flex:none}
.brand-name{font-family:"Rajdhani",sans-serif;font-weight:700;font-size:21px;color:var(--orange);line-height:1}
.nav-links{position:absolute;top:0;height:73px;display:flex;align-items:center;list-style:none}
.nav-links li{position:absolute;font-family:"Rajdhani",sans-serif;font-weight:600;font-size:16px;color:var(--white);letter-spacing:.5px;white-space:nowrap;top:27px}
.hero-title{position:absolute;left:44px;top:222px;font-family:"Rajdhani",sans-serif;font-weight:600;font-size:72px;color:var(--white);letter-spacing:2px;line-height:1}
.hero-sub{position:absolute;left:46px;top:298px;font-family:"Rajdhani",sans-serif;font-weight:500;font-size:36px;color:var(--white);letter-spacing:3px;line-height:1}
.hero-text{position:absolute;left:46px;top:358px;width:470px;font-size:14px;line-height:22px;color:var(--white)}
.btn{position:absolute;height:47px;display:flex;align-items:center;justify-content:center;font-family:"Rajdhani",sans-serif;font-weight:600;font-size:16px;letter-spacing:1px;color:var(--white)}
.btn-solid{background:var(--orange)}
.btn-ghost{border:2px solid var(--white)}
/* section headings */
.sec-title{position:absolute;left:0;width:1200px;text-align:center;font-family:"Raleway",sans-serif;font-weight:700;font-size:34px;color:var(--ink)}
.sec-sub{position:absolute;left:0;width:1200px;text-align:center;font-family:"Raleway",sans-serif;font-size:22px;color:#777}
.divider{position:absolute;width:110px;height:12px}
/* solutions */
.sol-photo{position:absolute;width:433px;height:268px;border:2px solid var(--orange)}
.sol-card{position:absolute;width:409px;height:265px;background:var(--orange);color:var(--white);text-align:center;padding:38px 30px 0}
.sol-card h3{font-family:"Raleway",sans-serif;font-weight:600;font-size:27px;letter-spacing:1px;margin-bottom:12px}
.sol-card p{font-size:13.5px;line-height:20px}
.frame-link{position:absolute;left:50%;transform:translateX(-50%);bottom:24px;width:92px;height:50px;display:flex;align-items:center;justify-content:center;font-size:13px}
.frame-link svg{position:absolute;inset:0}
/* about */
.about{position:absolute;left:0;top:1242px;width:1200px;height:430px;background:var(--mist)}
.about h2{position:absolute;left:44px;top:34px;font-family:"Raleway",sans-serif;font-weight:700;font-size:34px;color:var(--ink)}
.about h4{position:absolute;left:44px;top:80px;font-family:"Raleway",sans-serif;font-weight:700;font-size:21px;color:#666}
.about-copy{position:absolute;left:44px;top:152px;width:690px;font-size:13px;line-height:21px;color:#444}
.about-copy p+p{margin-top:14px}
.about-art{position:absolute;left:725px;top:30px;width:431px;height:390px;background:radial-gradient(circle at 55% 45%,#dfe8d3 0%,#eef1ea 55%,var(--mist) 75%)}
/* products */
.products{position:absolute;left:0;top:1672px;width:1200px;height:553px;background:linear-gradient(180deg,#2b2b2b,#1e1e1e)}
.products .sec-title,.products .sec-sub{color:var(--white)}
.products .sec-sub{font-weight:700;font-size:22px}
.prod{position:absolute;top:189px;width:261px;height:246px;background:var(--white)}
.prod-img{height:195px}
.prod-name{height:51px;display:flex;align-items:center;justify-content:center;font-size:15px;color:#333}
.prod-more{position:absolute;left:81px;top:82px;width:96px;height:30px;background:var(--orange);color:var(--white);font-size:12px;display:flex;align-items:center;justify-content:center}
.dots{position:absolute;left:527px;top:505px;display:flex;gap:8px}
.dots span{width:44px;height:4px;background:#bbb}
.dots span.on{background:var(--orange)}
/* mission */
.mission-item h5{font-family:"Raleway",sans-serif;font-weight:700;font-size:20px;color:var(--ink);margin-bottom:10px}
.mission-item p{font-size:13px;line-height:20px;color:#666}
.mission-item a{display:block;margin-top:6px;font-size:13px;font-weight:600;color:var(--orange);text-decoration:none}
.ring{position:absolute;width:144px;height:144px;border-radius:50%;border:2px solid #d8d8d8;background:var(--white);display:flex;align-items:center;justify-content:center}
/* quote */
.quote{position:absolute;left:0;top:2816px;width:1200px;height:152px;background:var(--slate);text-align:center}
.quote .q1{position:absolute;top:38px;width:100%;font-family:"Raleway",sans-serif;font-weight:700;font-size:28px;color:var(--orange)}
.quote .q2{position:absolute;top:84px;width:100%;font-family:"Raleway",sans-serif;font-size:29px;color:var(--white)}
/* footer */
.footer{position:absolute;left:0;top:2968px;width:1200px;height:377px;background:var(--orange);color:var(--white)}
.footer-base{position:absolute;left:0;top:3345px;width:1200px;height:344px;background:var(--slate)}
.fcol{position:absolute;top:36px}
.fcol h6{font-family:"Rajdhani",sans-serif;font-weight:700;font-size:22px;letter-spacing:.5px;margin-bottom:14px}
.fcol p{font-size:13px;line-height:20px}
.fcol ul{list-style:none;font-size:14px;line-height:25px}
.fcol li::before{content:"";display:inline-block;border-left:6px solid var(--white);border-top:4px solid transparent;border-bottom:4px solid transparent;margin-right:9px}
.news-input{width:246px;height:36px;background:var(--white);color:#aaa;font-size:13px;padding:9px 10px;margin-top:10px}
.news-btn{margin:10px 0 0 160px;width:86px;height:34px;background:var(--slate);font-size:13px;display:flex;align-items:center;justify-content:center}
.contact-row{display:flex;align-items:center;gap:10px;font-size:14px;margin-bottom:18px}
.hello{position:absolute;left:57px;top:3216px;width:1079px;height:386px;background:var(--white)}
.hello h2{position:absolute;top:44px;width:100%;text-align:center;font-family:"Rajdhani",sans-serif;font-weight:600;font-size:36px;letter-spacing:1px;color:var(--ink)}
.field{position:absolute;background:#f0f0f0;border:1px solid #e2e2e2;font-size:12px;color:#888;padding:11px 18px}
.submit{position:absolute;left:449px;top:300px;width:158px;height:47px;background:var(--orange);color:var(--white);font-family:"Rajdhani",sans-serif;font-weight:700;font-size:16px;letter-spacing:1px;display:flex;align-items:center;justify-content:center}
.copyright{position:absolute;left:64px;top:3641px;font-size:14px;color:#ddd}
.social{position:absolute;left:951px;top:3628px;display:flex;gap:10px}
.social span{width:30px;height:30px;border-radius:50%;border:2px solid #ddd}
</style>
</head>
<body>

<header class="hero">
  <div class="hero-photo" role="img" aria-label="Engineers in hard hats reviewing a laptop beside rooftop solar panels under a blue sky"></div>
  <div class="hero-shade"></div>
  <nav class="navbar">
    <div class="brand"><span class="brand-dot"></span><span class="brand-name">Tallow Ridge Energy</span></div>
    <ul class="nav-links">
      <li style="left:522px">HOME</li>
      <li style="left:620px">SOLUTIONS</li>
      <li style="left:760px">PRODUCTS</li>
      <li style="left:898px">ABOUT</li>
      <li style="left:1004px">CONTACT</li>
    </ul>
  </nav>
  <h1 class="hero-title">SOLAR ENERGY</h1>
  <p class="hero-sub">DOESN'T COST THE EARTH</p>
  <p class="hero-text">Solar Energy projects are financially feasible, socially beneficial, environmental friendly and generate value for its promoters, customers and community at large.</p>
  <a class="btn btn-solid" style="left:44px;top:462px;width:160px">LEARN MORE</a>
  <a class="btn btn-ghost" style="left:221px;top:462px;width:158px">CONTACT NOW</a>
</header>

<section class="solutions">
  <h2 class="sec-title" style="top:694px">Solar Solutions</h2>
  <p class="sec-sub" style="top:740px">Engineering, Procurement, and Construction</p>
  <svg class="divider" style="left:545px;top:781px" viewBox="0 0 110 12"><path d="M0 6H44l4-4 4 8 4-8 4 8 4-4H110" fill="none" stroke="#f15a24" stroke-width="1.5"/></svg>

  <div class="sol-photo" style="left:69px;top:851px;background:linear-gradient(135deg,#555 0%,#8a8a8a 50%,#c9b48a 100%)" role="img" aria-label="Commercial building signage"></div>
  <div class="sol-card" style="left:152px;top:888px">
    <h3>COMMERCIAL</h3>
    <p>Norwick Engineers set the benchmark for civil engineering design for residential, commercial and industrial projects.</p>
    <a class="frame-link"><svg viewBox="0 0 92 50"><path d="M1 10V1h10M81 1h10v9M91 40v9H81M11 49H1v-9" fill="none" stroke="#fff" stroke-width="1.5"/></svg>Read More</a>
  </div>

  <div class="sol-photo" style="left:634px;top:851px;background:linear-gradient(160deg,#7fa3cc 0%,#c5d6e8 45%,#4d5e74 100%)" role="img" aria-label="Residential towers against a cloudy sky"></div>
  <div class="sol-card" style="left:733px;top:888px">
    <h3>RESIDENTIAL</h3>
    <p>We help navigate the complexities of publicly funded projects to minimize risk and accelerate project completion.</p>
    <a class="frame-link"><svg viewBox="0 0 92 50"><path d="M1 10V1h10M81 1h10v9M91 40v9H81M11 49H1v-9" fill="none" stroke="#fff" stroke-width="1.5"/></svg>Read More</a>
  </div>
</section>

<section class="about">
  <h2>About Us</h2>
  <h4>Solar Expertise. Delivered.</h4>
  <svg class="divider" style="left:44px;top:114px" viewBox="0 0 110 12"><path d="M0 6H44l4-4 4 8 4-8 4 8 4-4H110" fill="none" stroke="#f15a24" stroke-width="1.5"/></svg>
  <div class="about-copy">
    <p>Tallow Ridge Energy is a national company that specialises in solar solutions for the commercial market. We also provide solutions for the residential market, bringing our uncompromising quality and service to the home. The founder of the company has over 10 years experience delivering projects on both a residential and commercial scale, having overseen the installation of more than 3 megawatts of solar projects. They were a pioneer on the first megawatt scale project in Australia.</p>
    <p>As a leader in the field, we offer cutting edge solar technology backed by industry leading warranties. All our systems are designed and installed by Grid Accord Council accredited persons. Our award winning designer will ensure your system will give the best long term performance and return on investment.</p>
  </div>
  <div class="about-art" role="img" aria-label="Illustration of a hand holding a tablet with green grass, a tree and wind turbines"></div>
</section>

<section class="products">
  <h2 class="sec-title" style="top:40px">Solar Products</h2>
  <p class="sec-sub" style="top:82px">Engineering, Procurement, and Construction</p>
  <svg class="divider" style="left:545px;top:124px" viewBox="0 0 110 12"><path d="M0 6H44l4-4 4 8 4-8 4 8 4-4H110" fill="none" stroke="#ffffff" stroke-width="1.5"/></svg>

  <div class="prod" style="left:47px">
    <div class="prod-img" style="background:linear-gradient(180deg,#6f8fb2 0%,#b8693f 60%,#3d4a3a 100%)" role="img" aria-label="House roof with solar panels"></div>
    <div class="prod-name">Solar Panels</div>
    <div class="prod-more">Read More</div>
  </div>
  <div class="prod" style="left:330px">
    <div class="prod-img" style="background:linear-gradient(160deg,#e8f2fb 0%,#6fa9dc 45%,#1f4f8c 100%)" role="img" aria-label="Solar inverters beside a solar array"></div>
    <div class="prod-name">Solar Inverters</div>
  </div>
  <div class="prod" style="left:612px">
    <div class="prod-img" style="background:linear-gradient(180deg,#9aa9bf 0%,#4b5d7a 55%,#c9c75a 100%)" role="img" aria-label="Technician checking a solar panel array"></div>
    <div class="prod-name">Monitoring systems</div>
  </div>
  <div class="prod" style="left:895px">
    <div class="prod-img" style="background:linear-gradient(90deg,#7a4a3a 0%,#a86a50 40%,#e3e0dc 70%,#cfcac4 100%)" role="img" aria-label="Wall mounted home battery unit"></div>
    <div class="prod-name">Batteries - RW</div>
  </div>
  <div class="dots"><span></span><span class="on"></span><span></span></div>
</section>

<section class="mission">
  <h2 class="sec-title" style="top:2263px">Our Mission</h2>
  <p class="sec-sub" style="top:2308px;font-weight:700;color:#666">Solar O&amp;M and Telecom O&amp;M</p>
  <svg class="divider" style="left:545px;top:2349px" viewBox="0 0 110 12"><path d="M0 6H44l4-4 4 8 4-8 4 8 4-4H110" fill="none" stroke="#f15a24" stroke-width="1.5"/></svg>

  <svg class="abs" style="left:576px;top:2398px" width="46" height="360" viewBox="0 0 46 360">
    <rect x="15" y="0" width="16" height="358" rx="8" fill="#b5b5b5"/>
    <path d="M31 68 L46 82 L31 96 Z" fill="#b5b5b5"/>
    <path d="M15 246 L0 260 L15 274 Z" fill="#b5b5b5"/>
  </svg>

  <div class="abs mission-item" style="left:250px;top:2428px;width:279px;text-align:right">
    <h5>Eco-Friendly</h5>
    <p>Lorem ipsum dolor sit amet, consectetur adipisicing elit. Cum consectetur sit ullam perspiciatis, deserunt.</p>
    <a>Read more</a>
  </div>
  <div class="ring" style="left:658px;top:2409px">
    <svg width="64" height="64" viewBox="0 0 64 64" fill="none" stroke="#555" stroke-width="2.5"><circle cx="32" cy="32" r="9"/><path d="M32 8v8M32 48v8M8 32h8M48 32h8M15 15l6 6M43 43l6 6M15 49l6-6M43 21l6-6"/><circle cx="32" cy="32" r="18"/></svg>
  </div>

  <div class="ring" style="left:385px;top:2586px">
    <svg width="64" height="64" viewBox="0 0 64 64" fill="none" stroke="#555" stroke-width="2.5"><circle cx="32" cy="22" r="4"/><path d="M22 12a14 14 0 0 0 0 20M42 12a14 14 0 0 1 0 20M16 6a22 22 0 0 0 0 32M48 6a22 22 0 0 1 0 32M32 26L20 58M32 26l12 32M24 46h16"/></svg>
  </div>
  <div class="abs mission-item" style="left:657px;top:2626px;width:279px">
    <h5>Wind Generators</h5>
    <p>Lorem ipsum dolor sit amet, consectetur adipisicing elit. Cum consectetur sit ullam perspiciatis, deserunt.</p>
    <a>Read more</a>
  </div>
</section>

<section class="quote">
  <p class="q1">Customers are no longer buying products and services.</p>
  <p class="q2">They are buying experiences, delivered via the product and services.</p>
</section>

<footer>
  <div class="footer">
    <div class="fcol" style="left:64px;width:270px">
      <h6>ABOUT US</h6>
      <p>Tallow Ridge Energy is a national company that specialises in solar solutions for the commercial market. We also provide solutions for the residential market, bringing our uncompromising quality and service to the home.</p>
    </div>
    <div class="fcol" style="left:403px">
      <h6>COMPANY</h6>
      <ul><li>About Us</li><li>Our Team</li><li>Career</li><li>Contact Us</li><li>Portfolio</li></ul>
    </div>
    <div class="fcol" style="left:595px;width:260px">
      <h6>NEWSLETTER</h6>
      <p>Lorem Ipsum is simply dummy text of the printing and.</p>
      <div class="news-input">Enter Your Email</div>
      <div class="news-btn">Subscribe</div>
    </div>
    <div class="fcol" style="left:927px;width:260px">
      <h6>CONTACT US</h6>
      <div class="contact-row"><svg width="16" height="16" viewBox="0 0 16 16"><path d="M4 1l3 3-2 2a9 9 0 0 0 5 5l2-2 3 3-2 3C7 15 1 9 1 3z" fill="#fff"/></svg>1800 7 BIRCH</div>
      <div class="contact-row"><svg width="14" height="18" viewBox="0 0 14 18"><path d="M7 0a7 7 0 0 1 7 7c0 5-7 11-7 11S0 12 0 7a7 7 0 0 1 7-7z" fill="#fff"/><circle cx="7" cy="7" r="2.5" fill="#f15a24"/></svg>sales@tallowridgeenergy.com.au</div>
    </div>
  </div>
  <div class="footer-base"></div>

  <div class="hello">
    <h2>SAY HELLO</h2>
    <div class="field" style="left:61px;top:106px;width:462px;height:39px">Full Name</div>
    <div class="field" style="left:61px;top:168px;width:462px;height:39px">Email Address</div>
    <div class="field" style="left:61px;top:227px;width:462px;height:39px">Phone Number</div>
    <div class="field" style="left:555px;top:106px;width:465px;height:160px">Your Message</div>
    <div class="submit">SUBMIT</div>
  </div>

  <p class="copyright">All rights reserved. © 2015-2016 Tallow Ridge Energy. Ltd.</p>
  <div class="social"><span></span><span></span><span></span><span></span><span></span></div>
</footer>

</body>
</html>
```